I need a business card design for a new dance business. I offer classical Indian dance tuition and also professional performances. I want to offer the community a variety of Indian dance experiences which include: group class and private tuition, school and preschool educational courses and workshops. dance theatre performances, community function workshops and performances, Kids Bollywood parties, wedding & conference performances, mouth percussion classes, Indian mythology/ dance costume and make up workshops.
The final design should communicate a feeling and impression of the vibrance and energy of Indian dance.
Updates
Hi Everyone,
Project Deadline Extended
Reason: I would like to refine a few changes to the details of this lovely design and we have run out of time!
Project Deadline Extended
Reason: Still waiting to hear back form designer re two possible changes to the card design. Tomorrow is the deadline and I have sent several messages but with no response. I need to see this through before selecting this lovely design.
Thank you.
Tara
Industry/Entity Type
Preschool
Requirements
Must have
- The front of the business card should have the photo of me (my face and torso), surrounded entirely by a border of bright magenta (to match the magenta of my lipstick - it is the same as the magenta on my skirt in the second photo). Within the top border I want (perhaps yellow-gold) writing to say "Tara Holloway - Artistic Director" and within the bottom border it should read "Saffron Lantern Indian Dance." If you turn the card on its side the left border should have my telephone number: 0417 862 493 and the right-hand border should read: saffronlanternindiandance@quillmail.example
The reverse of the card should be the orange of the dance costume
and I'd like the picture of my feet and legs to be on the right side of the back of the card as a side border. Centre-aligned on the orange background it should read (perhaps in dark magenta):
Indian dance classes + private tuition
School + preschool educational courses and workshops
Dance theatre performances
Community function workshops and performances
Children's Bollywood parties
Wedding + conference performances
Mouth percussion classes
Indian mythology and dance demonstration workshops
Dance costume and make-up workshops
Nice to have
- A lovely artistic but easy-to-read font would be nice.

```html
<!DOCTYPE html>
<html lang="en">
<head>
<meta charset="utf-8">
<title>Saffron Lantern Indian Dance</title>
<link rel="stylesheet" href="https://fonts.googleapis.com/css2?family=Macondo&family=Delius&display=swap">
<style>
  :root {
    --magenta: #9a1b5c;
    --magenta-deep: #7e1249;
    --magenta-pattern: #a8246a;
    --gold: #f2b31d;
    --gold-light: #f6c83a;
    --gold-deep: #e3a20f;
    --text-dark: #6e0d3a;
    --photo-red: #b8203c;
    --photo-orange: #e07a26;
  }
  * { margin: 0; padding: 0; box-sizing: border-box; }
  html, body { width: 926px; height: 1200px; overflow: hidden; background: #ffffff; }
  .card {
    position: relative;
    width: 926px;
    height: 1200px;
    overflow: hidden;
    font-family: "Delius", sans-serif;
  }
  .top-band {
    position: absolute;
    left: 0; top: 0;
    width: 926px; height: 600px;
    background: var(--magenta-deep);
  }
  .photo-legs {
    position: absolute;
    left: 0; top: 0;
    width: 282px; height: 600px;
    background: linear-gradient(160deg, #d9c9c2 0%, var(--photo-red) 38%, #8d1b3a 62%, var(--photo-orange) 85%, #d8c0b4 100%);
  }
  .title-panel {
    position: absolute;
    left: 282px; top: 0;
    width: 552px; height: 600px;
    background: radial-gradient(ellipse at 50% 45%, var(--magenta-pattern) 0%, var(--magenta) 70%);
    color: var(--gold);
    text-align: center;
  }
  .name {
    font-family: "Macondo", cursive;
    font-size: 46px;
    font-weight: 400;
    letter-spacing: 2px;
    margin-top: 40px;
    line-height: 1.1;
  }
  .credential {
    font-family: "Macondo", cursive;
    font-size: 22px;
    letter-spacing: 1.5px;
    line-height: 1.35;
    margin-top: 18px;
  }
  .figures {
    width: 300px;
    height: 150px;
    margin: 40px auto 0;
    background: linear-gradient(180deg, var(--gold-light), var(--gold-deep));
    border-radius: 60px 60px 10px 10px;
  }
  .business-name {
    font-family: "Macondo", cursive;
    font-weight: 400;
    margin-top: 90px;
    line-height: 1.15;
  }
  .business-name .line-one { display: block; font-size: 32px; letter-spacing: 2px; }
  .business-name .line-two { display: block; font-size: 42px; letter-spacing: 2px; }
  .contact-strip {
    position: absolute;
    left: 834px; top: 0;
    width: 92px; height: 600px;
    background: var(--magenta-deep);
    overflow: hidden;
  }
  .contact-strip .contact {
    position: absolute;
    left: 66px; top: 18px;
    transform-origin: 0 0;
    transform: rotate(90deg);
    display: flex;
    align-items: baseline;
    white-space: nowrap;
    color: var(--gold);
    font-family: "Delius", sans-serif;
    line-height: 1;
  }
  .phone { font-size: 30px; letter-spacing: 2px; }
  .email { font-size: 14.5px; margin-left: 18px; }
  .bottom-band {
    position: absolute;
    left: 0; top: 600px;
    width: 926px; height: 600px;
    background: radial-gradient(ellipse at 30% 50%, var(--gold-light) 0%, var(--gold) 55%, var(--gold-deep) 100%);
  }
  .services {
    position: absolute;
    left: 60px; top: 95px;
    width: 440px;
    list-style: none;
    text-align: center;
    color: var(--text-dark);
    font-size: 21px;
    line-height: 33px;
  }
  .photo-dancer {
    position: absolute;
    left: 552px; top: 0;
    width: 374px; height: 600px;
    background: linear-gradient(180deg, #e8e2dc 0%, #e5d7cf 25%, var(--photo-orange) 45%, var(--photo-red) 75%, #f0b43a 100%);
  }
</style>
</head>
<body>
  <div class="card">
    <section class="top-band">
      <div class="photo-legs" role="img" aria-label="Photograph of a dancer's legs and feet in a red and gold costume"></div>
      <div class="title-panel">
        <h1 class="name">Tara Holloway</h1>
        <p class="credential">Graduate of Kuchipudi<br>Classical Indian Dance</p>
        <div class="figures" role="img" aria-label="Illustration of three seated meditating figures in gold"></div>
        <h2 class="business-name">
          <span class="line-one">Saffron Lantern</span>
          <span class="line-two">Indian Dance</span>
        </h2>
      </div>
      <div class="contact-strip">
        <p class="contact"><span class="phone">0417 862 493</span><span class="email">saffronlanternindiandance@quillmail.example</span></p>
      </div>
    </section>
    <section class="bottom-band">
      <ul class="services">
        <li>Indian dance classes + private tuition</li>
        <li>School + preschool educational courses and workshops</li>
        <li>Dance theatre performances</li>
        <li>Community function workshops and performances</li>
        <li>Children's Bollywood parties</li>
        <li>Wedding + conference performances</li>
        <li>Mouth percussion classes</li>
        <li>Indian mythology and dance demonstration workshops</li>
        <li>Dance costume and make-up workshops</li>
      </ul>
      <div class="photo-dancer" role="img" aria-label="Photograph of a classical Indian dancer posing in an orange and red costume"></div>
    </section>
  </div>
</body>
</html>
```